Designing a brochures for an educational counseling service provider

We would like a 4 sided design on a 11x8.5 paper, half folded. I have including a sample design we did to give you an idea of what we envision but we welcome creativity to make beautiful looking flyers. Text for the flier is included as well as our logo.
- The most important thing is capturing our audience/market. We will be handing these flies to schools, organizations and individual clients.

www.pvrlearningadvisors.example

Target Market(s)

We are targeting international students wanting to study in the U.S and Canada.

Industry/Entity Type

Education

Requirements
Must have
• - Clean and clear
• - Our logo should visible and well placed.
• - Could you the pictures of students, libraries and school buildings or you could use the pictures we already have.
Nice to have
• We would like this to match business cards.

```html
<!DOCTYPE html>
<html lang="en">
<head>
<meta charset="utf-8">
<title>PVR Learning Advisors – Brochure Inside Spread</title>
<link href="https://fonts.googleapis.com/css2?family=Open+Sans:ital,wght@0,400;0,600;0,700;1,400&family=Roboto+Condensed:ital,wght@0,400;0,700;1,400;1,700&display=swap" rel="stylesheet">
<style>
  :root{
    --stage:#4b4b4b;
    --paper:#ffffff;
    --paper-shade:#eef0f3;
    --blue:#0a5cae;
    --blue-bright:#1680cf;
    --navy:#0b2f6b;
    --ink-dark:#0c1c33;
    --orange:#f07f21;
    --orange-deep:#e0621a;
    --text:#3a3f47;
    --heading-blue:#1c5fae;
  }
  *{box-sizing:border-box;margin:0;padding:0}
  html,body{width:1200px;height:1200px;overflow:hidden;background:var(--stage)}
  body{position:relative;font-family:"Open Sans",Arial,sans-serif;color:var(--text)}
  .spread{position:absolute;left:60px;top:182px;width:1080px;height:835px;display:flex;box-shadow:0 20px 50px rgba(0,0,0,.45)}
  .page{position:relative;width:540px;height:835px;background:var(--paper);overflow:hidden}
  .page--left{background:linear-gradient(90deg,#fff 85%,var(--paper-shade))}
  .page--right{background:linear-gradient(90deg,var(--paper-shade),#fff 15%)}
  .page-art{position:absolute;inset:0;width:540px;height:835px}
  .title-tab{position:absolute;font-family:"Roboto Condensed",Arial,sans-serif;font-weight:700;color:#fff;text-transform:uppercase;letter-spacing:1px;line-height:1}
  .company-band{position:absolute;font-family:"Roboto Condensed",Arial,sans-serif;font-style:italic;color:#fff;font-size:20px;line-height:1.2;white-space:nowrap}
  .about-copy{position:absolute;left:266px;top:162px;width:250px;font-size:10.5px;line-height:1.55;text-align:justify}
  .about-copy p+p{margin-top:10px}
  .brand{position:absolute;left:286px;top:462px;display:flex;align-items:center;gap:10px}
  .brand-dot{width:30px;height:30px;border-radius:50%;background:var(--blue);flex:none}
  .brand-name{font-family:"Open Sans",Arial,sans-serif;font-weight:700;font-size:15px;color:var(--blue);line-height:1.15}
  .quote-box{position:absolute;left:56px;top:585px;width:430px;height:132px;background:rgba(8,22,42,.9);color:#fff;padding:18px 26px 0 92px}
  .quote-mark{position:absolute;left:24px;top:2px;font-family:"Roboto Condensed",Arial,sans-serif;font-weight:700;font-size:96px;line-height:1}
  .quote-text{font-family:"Roboto Condensed",Arial,sans-serif;font-style:italic;font-size:21px;line-height:1.35}
  .site{position:absolute;font-family:"Open Sans",Arial,sans-serif;font-weight:600;color:#fff;font-size:16px;letter-spacing:1.5px;white-space:nowrap}
  .services-copy{position:absolute;left:36px;top:152px;width:470px;font-size:10px;line-height:1.45}
  .services-copy .lead{margin-bottom:8px}
  .label{font-family:"Roboto Condensed",Arial,sans-serif;font-weight:700;font-style:italic;text-transform:uppercase;font-size:12.5px;letter-spacing:.4px}
  .label--orange{color:var(--orange-deep)}
  .label--blue{color:var(--heading-blue)}
  .label--white{color:#fff}
  .package{list-style:none;margin:2px 0 8px}
  .package li{position:relative;padding-left:12px}
  .package li::before{content:"";position:absolute;left:1px;top:6px;width:5px;height:5px;border-radius:50%;background:var(--orange)}
  .service{position:relative;padding-left:16px;margin-bottom:8px}
  .service::before{content:"";position:absolute;left:0;top:3px;width:0;height:0;border-left:8px solid var(--heading-blue);border-top:5px solid transparent;border-bottom:5px solid transparent}
  .services-blue{position:absolute;left:36px;top:618px;width:470px;font-size:10px;line-height:1.45;color:#fff}
  .services-blue .service::before{border-left-color:#fff}
</style>
</head>
<body>
<main class="spread">

  <section class="page page--left">
    <svg class="page-art" viewBox="0 0 540 835" aria-hidden="true">
      <defs>
        <linearGradient id="deepBlue" x1="0" y1="0" x2="1" y2="1">
          <stop offset="0" stop-color="#1a7fd0"/><stop offset="1" stop-color="#0b2f6b"/>
        </linearGradient>
      </defs>
      <polygon points="215,38 540,38 540,100 175,100" fill="var(--orange)"/>
      <polygon points="0,68 252,68 210,140 0,140" fill="var(--blue)"/>
      <polygon points="252,68 262,68 220,140 210,140" fill="#fff"/>
      <polygon points="0,540 540,510 540,835 0,835" fill="url(#deepBlue)"/>
      <polygon points="0,770 540,735 540,835 0,835" fill="var(--orange)"/>
      <polygon points="0,790 540,755 540,835 0,835" fill="var(--orange-deep)"/>
    </svg>
    <div class="title-tab" style="left:26px;top:88px;font-size:32px">About Us</div>
    <div class="company-band" style="left:250px;top:56px">PVR Learning Advisors, LLC</div>

    <svg style="position:absolute;left:0;top:520px" width="540" height="230" role="img" aria-label="Photo of library bookshelves in blue tones">
      <defs><linearGradient id="libraryTone" x1="0" y1="0" x2="1" y2="1">
        <stop offset="0" stop-color="#2d86cc" stop-opacity=".7"/><stop offset="1" stop-color="#0b3a7a" stop-opacity=".3"/>
      </linearGradient></defs>
      <polygon points="0,20 540,-10 540,230 0,230" fill="url(#libraryTone)"/>
    </svg>

    <svg style="position:absolute;left:20px;top:160px" width="230" height="420" role="img" aria-label="Photo of a smiling student with a backpack holding yellow folders">
      <defs><linearGradient id="studentTone" x1="0" y1="0" x2="0" y2="1">
        <stop offset="0" stop-color="#e9d2bd"/><stop offset=".55" stop-color="#e8b83a"/><stop offset="1" stop-color="#5b7aa6"/>
      </linearGradient></defs>
      <rect width="230" height="420" rx="4" fill="url(#studentTone)"/>
    </svg>

    <div class="about-copy">
      <p>Our mission is to make quality education accessible and affordable to the families we serve. Our services are designed with the child's future in mind. Whether one is seeking an academic or non-academic environment, it is important to us that we set our clients up for success.</p>
      <p>We are a family-centered organization and our goals are the same as those of our clients: for their child to thrive and reach their goals and dreams. With over 10 years of experience in this business, we are aware of the financial obstacles created by the ever increasing cost in education. Our expert consultants work closely with families to map out their educational budget and find the best affordable and quality educational options.</p>
    </div>

    <div class="brand"><span class="brand-dot"></span><span class="brand-name">PVR Learning<br>Advisors</span></div>

    <div class="quote-box">
      <div class="quote-mark">&ldquo;</div>
      <p class="quote-text">We offer comprehensive services to families, students, institutions and governmental organizations.</p>
    </div>
    <div class="site" style="left:150px;top:792px">www.pvrlearningadvisors.example</div>
  </section>

  <section class="page page--right">
    <svg class="page-art" viewBox="0 0 540 835" aria-hidden="true">
      <defs>
        <linearGradient id="waveBlue" x1="0" y1="0" x2="1" y2="1">
          <stop offset="0" stop-color="#1a82d2"/><stop offset="1" stop-color="#0b2f6b"/>
        </linearGradient>
      </defs>
      <polygon points="0,68 190,68 150,140 0,140" fill="var(--orange)"/>
      <polygon points="205,38 540,38 540,100 170,100" fill="var(--navy)"/>
      <polygon points="218,38 540,38 540,60 206,60" fill="var(--blue-bright)"/>
      <path d="M0,600 C180,580 360,540 540,505 L540,835 L0,835 Z" fill="url(#waveBlue)"/>
      <polygon points="0,800 540,768 540,835 0,835" fill="var(--orange)"/>
      <polygon points="0,812 540,782 540,835 0,835" fill="var(--orange-deep)"/>
    </svg>
    <div class="title-tab" style="left:18px;top:91px;font-size:30px">Services</div>
    <div class="company-band" style="left:248px;top:68px;font-size:18px">PVR Learning Advisors, LLC</div>

    <div class="services-copy">
      <p class="lead">Finding the right school or program for your child is one of the most important decisions your family will make. The right choice will make a major impact on your child's future.</p>
      <p class="label label--orange">Our package includes:</p>
      <ul class="package">
        <li>Intake interview</li>
        <li>Present range of options based on needs and goals of the family</li>
        <li>Interview coaching</li>
        <li>Assistance with application and essays</li>
        <li>Updates on student progress throughout their enrollment with the school</li>
        <li>Advisement on financial documents and visa applications</li>
      </ul>
      <div class="service">
        <p class="label label--blue">Boarding schools:</p>
        <p>Students who want the best out of their grade school experience are likely to choose boarding schools because they are proven to better prepare students for university. North American boarding schools provide a quality dynamic experience that will facilitate personal growth in independence, leadership, and confidence as well as provide the academic curriculum necessary to prepare students for university.</p>
      </div>
      <div class="service">
        <p class="label label--blue">College admission:</p>
        <p>At our firm, we specialize in college/university admissions and we understand how confusing, time-consuming, and stressful the application process can be. Our experienced counselors are here to answer your questions and guide you step by step. Parents and students may have limited access to information on schools and may not know how to begin; our counselors have a solution.</p>
      </div>
    </div>

    <div class="services-blue">
      <div class="service">
        <p class="label label--white">Transfer students:</p>
        <p>Need to find a school or an alternative school that is a better match for you? We work with students and families to transfer from one school to another.</p>
      </div>
      <div class="service">
        <p class="label label--white">Scholarships:</p>
        <p>Funding the education for your children in some of the world's top schools can be very expensive as tuition and fees increase at an average of 4% every year. We work with you to set a budget and guide you through the financial aid process. Over 70% of our clients have been awarded scholarships or financial aid. Our consultants are members of GAAC, the leading association for educational consultants in North America.</p>
      </div>
    </div>
    <div class="site" style="left:215px;top:800px">www.pvrlearningadvisors.example</div>
  </section>

</main>
</body>
</html>
```